New word press website site design

We provide email marketing to aircraft brokers and dealers to assist in finding buyers for their aircraft.

Our target market to purchase our broadcasts are the aircraft sellers – NOT the buyers.

Our target market when sending the email broadcast, are the buyers (end users).

The website should target brokers and our email database targets the buyers.

We do not buy or sell aircraft as a company. We provide email marketing solutions to connect buyers and sellers of aircraft.

Our other site is planelantern.com and will be redesigned soon. Please use it as a reference as far as general scope but they layout can be completely different and should include helicopters only as far as imagery. The colors should be similar as the logos are similar, however we do NOT want both sites to be identical in use of primary color

Plenty of images and sample broadcasts attached to use as needed throughout the site.

Headlines listed below with some text copy.

In the event that we need to add more text, please use standard greek text as a place holder for the purposes of the mockup design.

Need to have a “SUBSCRIBE” button to join our mailing list.

Possible Headlines:

Exclusively Showcasing Rotor Wing Aircraft to the Global Marketplace

Showcasing Pre-Owned Helicopters Available For Sale, Lease, Trade, or Wanted for Acquisition.

Mobile-optimized Email Campaigns that Render Correctly Across all Devices

Targeted worldwide recipients that currently own, operate, or have an interest in rotor wing aircraft

STRONGEST Rotor Wing Database in the Industry

Text/Copy:

HOME
Rotorbay Vista is one of most powerful marketing tools in the industry to utilize in reaching targeted buyers of pre-owned helicopters. Rotorbay Vista provides the rotor wing aircraft market with a fast, effective, and affordable email broadcast solution to utilize in the marketing of Helicopters for sale.

Developed Exclusively to Showcase Rotor Wing Aircraft to the Global marketplace, Rotorbay Vista is a powerful tool designed to maximize leads and accelerate the sales process by providing the ability to reach a global network of Helicopter buyers in a matter of seconds.

DATABASE:

While Rotorbay Vista is delivered to all known broker/dealers, our primary focus is in reaching end users. Our opt-in/opt-out recipient database is updated daily and developed specifically to deliver the latest details on helicopters available for sale or lease to the inboxes of a global network of Helicopter buyers and sellers.

· Helicopter Owners

· Helicopter Operators

· Helicopter Charter Services

· Helicopter Management Companies

· Corporate/Municipal Flight Departments

· Helicopter Pilots

· Senior Aviation Executives

· Wealth Management Firms

· High Net Worth Individuals

· Helicopter Broker/Dealers

Helicopter Tour/Travel Firms

· Off Shore Oil & Gas Production Firms

· Municipalities/Media/Medevac Firms

Our recipient database is continuously updated and developed specifically to reach buyers and sellers of Helicopters. This ensures that your Helicopter will be showcased to the right people. Rotorbay Vista does not broadcast non-rotor wing aircraft and focuses exclusively on the Global Helicopter Market.

Broadcast Design:

Rotorbay Vista broadcast ads are custom designed for you by incorporating your corporate image and branding. Because you have worked hard in developing your corporate image, we strive to maintain it while designing an ad that will showcase your Helicopter to its best advantage. Rotorbay Vista utilizes Mobile-optimized Email Campaigns with Responsive Coding to render correctly across all devices

Once you have approved the design, we schedule the broadcast to be sent on the available date and time you request. The broadcast will link to your website and the results can be immediate. All email leads and replies will go to the email address that you provided.

Pricing:
Create a place holder for 3 Different Broadcast Packages

-Broadcast Package A
-Broadcast Package B
-Broadcast Package C

Target Market(s)

The target market is any person or company that has aircraft for sale. We work with brokers, dealers, and owners to assist in finding buyers for their aircraft using email marketing campaigns (Showcase broadcasts).

Industry/Entity Type

Aviation

Colors
0255a3
00a990

Requirements
Nice to have
• Samples of helicopter for sale broadcast ads in /image gallery/slider

```html
<!DOCTYPE html>
<html lang="en">
<head>
<meta charset="utf-8">
<title>Rotorbay Vista</title>
<link href="https://fonts.googleapis.com/css2?family=Roboto:wght@400;500;700&display=swap" rel="stylesheet">
<style>
:root{
  --navy:#0f2b4c;
  --navy-deep:#0b2240;
  --navy-mid:#163d66;
  --footer:#0c1828;
  --green:#7cc144;
  --green-dark:#6aaf35;
  --white:#ffffff;
  --muted:#b7c4d4;
  --grey:#dcdcdc;
  --text-dark:#333;
  --red:#e0242b;
}
*{box-sizing:border-box;margin:0;padding:0}
html,body{width:1200px;height:2995px;overflow:hidden}
body{font-family:'Roboto',Arial,sans-serif;background:var(--navy);color:var(--white);position:relative}
.abs{position:absolute}

/* header */
.site-header{position:absolute;top:0;left:0;width:1200px;height:80px;background:var(--navy-deep)}
.brand{position:absolute;left:220px;top:26px;display:flex;align-items:center;gap:10px;font-size:22px;font-weight:500;color:var(--white)}
.brand-dot{width:12px;height:12px;border-radius:50%;background:var(--green)}
.main-nav{position:absolute;left:440px;top:32px;display:flex;gap:20px;font-size:12px}
.main-nav a{color:var(--white);text-decoration:none}
.main-nav a.active{border-bottom:2px solid var(--green);padding-bottom:6px}
.header-phone{position:absolute;left:800px;top:32px;font-size:12px;font-weight:500;display:flex;align-items:center;gap:6px}
.btn-subscribe{position:absolute;left:900px;top:25px;width:82px;height:28px;background:var(--green);font-size:11px;font-weight:700;display:flex;align-items:center;justify-content:center}

/* hero */
.hero{position:absolute;top:80px;left:0;width:1200px;height:455px;background:linear-gradient(180deg,#26364a 0%,#6a6f6e 45%,#d8a35c 66%,#3f4630 76%,#29311f 100%)}
.hero h1{position:absolute;top:190px;width:100%;text-align:center;font-size:26px;font-weight:700;line-height:32px;text-shadow:0 2px 6px rgba(0,0,0,.6)}
.hero-dots{position:absolute;top:431px;left:550px;display:flex;gap:6px}
.hero-dots span{width:16px;height:3px;background:var(--white)}
.hero-dots span.on{background:var(--green)}

/* services */
.services{position:absolute;top:535px;left:0;width:1200px;height:620px;background:var(--navy)}
.section-title{position:absolute;width:100%;text-align:center;font-size:24px;font-weight:700}
.lead{position:absolute;left:300px;width:600px;text-align:center;font-size:11px;line-height:16px;color:var(--muted)}
.services-media{position:absolute;left:220px;top:165px;width:500px;height:330px;background:linear-gradient(160deg,#6b8ab3 0%,#a9bed6 45%,#2a3440 70%,#5a6f86 100%)}
.audience{position:absolute;left:720px;top:165px;width:260px;height:330px;background:var(--green);padding:18px 0 0 20px;list-style:none}
.audience li{font-size:10.5px;height:22.8px;display:flex;align-items:center;gap:8px}
.audience svg{flex:none}

/* welcome */
.welcome{position:absolute;top:1155px;left:0;width:1200px;height:645px;background:linear-gradient(180deg,var(--navy-mid) 0,var(--navy-mid) 245px,var(--navy) 245px)}
.video-frame{position:absolute;left:220px;top:107px;width:760px;height:334px;border:5px solid var(--white);background:radial-gradient(ellipse at 50% 55%,#55595e 0%,#1c1d20 45%,#050505 100%)}
.play{position:absolute;left:353px;top:133px}
.col-text{position:absolute;top:465px;width:330px;font-size:11px;line-height:16px;color:var(--muted)}
.col-divider{position:absolute;left:600px;top:465px;width:1px;height:80px;background:#2f4d70}
.soft-rule{position:absolute;left:270px;top:610px;width:660px;height:10px;background:radial-gradient(ellipse at center,rgba(0,0,0,.45),transparent 70%)}

/* pricing */
.pricing{position:absolute;top:1800px;left:0;width:1200px;height:600px;background:var(--navy)}
.sub{position:absolute;top:72px;width:100%;text-align:center;font-size:11px;color:var(--muted)}
.plans{position:absolute;left:220px;top:145px;width:760px;height:410px;background:var(--white)}
.plan{position:absolute;top:0;width:253px;height:410px;color:var(--text-dark)}
.plan-head{height:65px;background:var(--navy);color:var(--white);font-size:18px;display:flex;align-items:center;justify-content:center;gap:5px}
.plan-head b{font-weight:700}
.plan-price{height:68px;background:var(--grey);font-size:22px;font-weight:700;display:flex;align-items:center;justify-content:center}
.plan ol{list-style:none;padding-top:22px}
.plan li{font-size:10.5px;height:30.5px;text-align:center;color:#555}
.plan-btn{position:absolute;left:27px;top:345px;width:200px;height:38px;background:var(--navy);color:var(--white);font-size:10.5px;font-weight:700;display:flex;align-items:center;justify-content:center}
.plan.featured{top:-20px;height:430px;background:var(--white);box-shadow:0 0 14px rgba(0,0,0,.25);z-index:2}
.plan.featured .plan-head{height:85px;background:var(--green);padding-top:20px}
.plan.featured .plan-btn{background:var(--green);top:365px}
.badge{position:absolute;left:76px;top:-8px;width:100px;height:22px;border-radius:11px;background:var(--red);color:var(--white);font-size:9px;font-weight:700;display:flex;align-items:center;justify-content:center}

/* broadcast design */
.design{position:absolute;top:2400px;left:0;width:1200px;height:333px;background:var(--green)}
.sample-a{position:absolute;left:220px;top:25px;width:238px;height:308px;border:4px solid var(--white);background:linear-gradient(180deg,#1a1a1a 0%,#b8251f 20%,#111 45%,#6b7a86 65%,#111 100%)}
.sample-b{position:absolute;left:410px;top:105px;width:202px;height:228px;border:4px solid var(--white);background:linear-gradient(180deg,#0c0c0c 0%,#2b3a5c 35%,#d8d8d8 60%,#111 100%)}
.design h2{position:absolute;left:675px;top:103px;font-size:24px;font-weight:700}
.design p{position:absolute;left:675px;top:145px;width:300px;font-size:11px;line-height:17px}
.btn-proof{position:absolute;left:675px;top:229px;width:163px;height:28px;background:var(--navy);font-size:10.5px;font-weight:700;display:flex;align-items:center;justify-content:center}

/* footer */
.site-footer{position:absolute;top:2733px;left:0;width:1200px;height:262px;background:var(--footer)}
.fcol{position:absolute;top:52px;font-size:11px;line-height:17px;color:var(--muted)}
.fcol h4{font-size:11px;font-weight:700;color:var(--white);margin-bottom:8px;letter-spacing:.3px}
.signup{position:absolute;left:740px;top:75px;width:240px;height:34px;background:var(--white);border:2px solid var(--white)}
.signup span{position:absolute;left:8px;top:8px;font-size:11px;color:#999}
.signup b{position:absolute;right:0;top:0;width:78px;height:30px;background:var(--green);color:var(--white);font-size:10.5px;display:flex;align-items:center;justify-content:center}
.social{position:absolute;left:740px;top:130px;display:flex;gap:8px}
.social span{width:24px;height:24px;background:#5b6673}
.copyright{position:absolute;top:219px;width:100%;text-align:center;font-size:11px;color:#7d8a99}
</style>
</head>
<body>

<header class="site-header">
  <div class="brand"><span class="brand-dot"></span>Rotorbay Vista</div>
  <nav class="main-nav">
    <a class="active">Home</a><a>Services</a><a>Broadcast Design</a><a>Pricing</a><a>Contact</a>
  </nav>
  <div class="header-phone">
    <svg width="11" height="11" viewBox="0 0 24 24"><path fill="#7cc144" d="M6.6 10.8a15 15 0 0 0 6.6 6.6l2.2-2.2c.3-.3.7-.4 1-.2 1.1.4 2.3.6 3.6.6.6 0 1 .4 1 1V20c0 .6-.4 1-1 1A17 17 0 0 1 3 4c0-.6.4-1 1-1h3.5c.6 0 1 .4 1 1 0 1.2.2 2.4.6 3.6.1.3 0 .7-.2 1z"/></svg>
    1800 555 014
  </div>
  <div class="btn-subscribe">SUBSCRIBE</div>
</header>

<section class="hero" role="img" aria-label="Helicopter parked on grass at sunset">
  <h1>Exclusively Showcasing Rotor Wing Aircraft<br>to the Global Marketplace</h1>
  <div class="hero-dots"><span class="on"></span><span></span><span></span><span></span><span></span></div>
</section>

<section class="services">
  <h2 class="section-title" style="top:50px">What Services We offer</h2>
  <p class="lead" style="top:92px">Rotorbay Vista is one of most powerful marketing tools in the industry to utilize in reaching targeted buyers of pre-owned helicopters. Rotorbay Vista provides the rotor wing aircraft market with a fast, effective, and affordable email broadcast solution to utilize in the marketing of Helicopters for sale.</p>
  <div class="services-media" role="img" aria-label="Two helicopters flying over snowy mountains"></div>
  <ul class="audience">
    <li><svg width="9" height="9" viewBox="0 0 10 10"><path d="M1 5l3 3 5-6" stroke="#fff" stroke-width="2" fill="none"/></svg>Helicopter Owners</li>
    <li><svg width="9" height="9" viewBox="0 0 10 10"><path d="M1 5l3 3 5-6" stroke="#fff" stroke-width="2" fill="none"/></svg>Helicopter Operators</li>
    <li><svg width="9" height="9" viewBox="0 0 10 10"><path d="M1 5l3 3 5-6" stroke="#fff" stroke-width="2" fill="none"/></svg>Helicopter Charter Services</li>
    <li><svg width="9" height="9" viewBox="0 0 10 10"><path d="M1 5l3 3 5-6" stroke="#fff" stroke-width="2" fill="none"/></svg>Helicopter Management Companies</li>
    <li><svg width="9" height="9" viewBox="0 0 10 10"><path d="M1 5l3 3 5-6" stroke="#fff" stroke-width="2" fill="none"/></svg>Corporate/Municipal Flight Departments</li>
    <li><svg width="9" height="9" viewBox="0 0 10 10"><path d="M1 5l3 3 5-6" stroke="#fff" stroke-width="2" fill="none"/></svg>Helicopter Pilots</li>
    <li><svg width="9" height="9" viewBox="0 0 10 10"><path d="M1 5l3 3 5-6" stroke="#fff" stroke-width="2" fill="none"/></svg>Senior Aviation Executives</li>
    <li><svg width="9" height="9" viewBox="0 0 10 10"><path d="M1 5l3 3 5-6" stroke="#fff" stroke-width="2" fill="none"/></svg>Wealth Management Firms</li>
    <li><svg width="9" height="9" viewBox="0 0 10 10"><path d="M1 5l3 3 5-6" stroke="#fff" stroke-width="2" fill="none"/></svg>High Net Worth Individuals</li>
    <li><svg width="9" height="9" viewBox="0 0 10 10"><path d="M1 5l3 3 5-6" stroke="#fff" stroke-width="2" fill="none"/></svg>Helicopter Broker/Dealers</li>
    <li><svg width="9" height="9" viewBox="0 0 10 10"><path d="M1 5l3 3 5-6" stroke="#fff" stroke-width="2" fill="none"/></svg>Helicopter Tour/Travel Firms</li>
    <li><svg width="9" height="9" viewBox="0 0 10 10"><path d="M1 5l3 3 5-6" stroke="#fff" stroke-width="2" fill="none"/></svg>Off Shore Oil &amp; Gas Production Firms</li>
    <li><svg width="9" height="9" viewBox="0 0 10 10"><path d="M1 5l3 3 5-6" stroke="#fff" stroke-width="2" fill="none"/></svg>Municipalities/Media/Medevac Firms</li>
  </ul>
  <p class="lead" style="top:524px">Our recipient database is continuously updated and developed specifically to reach buyers and sellers of Helicopters. This ensures that your Helicopter will be showcased to the right people. Rotorbay Vista does not broadcast non rotor wing aircraft and focuses exclusively on the Global Helicopter Market.</p>
</section>

<section class="welcome">
  <h2 class="section-title" style="top:50px">Welcome Rotorbay Vista</h2>
  <div class="video-frame" role="img" aria-label="Video still of a helicopter in a dark studio">
    <svg class="play" width="44" height="44" viewBox="0 0 44 44"><circle cx="22" cy="22" r="20" fill="none" stroke="#fff" stroke-width="3"/><path d="M17 13l13 9-13 9z" fill="#fff"/></svg>
  </div>
  <p class="col-text" style="left:220px">Rotorbay Vista is one of most powerful marketing tools in the industry to utilize in reaching targeted buyers of pre-owned helicopters. Rotorbay Vista provides the rotor wing aircraft market with a fast, effective, and affordable email broadcast solution to utilize in the marketing of Helicopters for sale.</p>
  <div class="col-divider"></div>
  <p class="col-text" style="left:642px">Developed Exclusively to Showcase Rotor Wing Aircraft to the Global marketplace, Rotorbay Vista is a powerful tool designed to maximize leads and accelerate the sales process by providing the ability to reach a global network of Helicopter buyers in a matter of seconds.</p>
  <div class="soft-rule"></div>
</section>

<section class="pricing">
  <h2 class="section-title" style="top:36px">3 Different Broadcast Packages</h2>
  <p class="sub">Our Broadcast Packages Pricing below listed:</p>
  <div class="plans">
    <div class="plan" style="left:0">
      <div class="plan-head">Broadcast <b>Package A</b></div>
      <div class="plan-price">$39.99</div>
      <ol><li>01. Awesome lorem ipsum dolor sit</li><li>02. Awesome lorem ipsum dolor sit</li><li>03. Awesome lorem ipsum dolor sit</li><li>04. Awesome lorem ipsum dolor sit</li><li>05. Awesome lorem ipsum dolor sit</li><li>06. Awesome lorem ipsum dolor sit</li></ol>
      <div class="plan-btn">SELECT PACKAGE</div>
    </div>
    <div class="plan featured" style="left:253px">
      <div class="badge">MOST POPULAR</div>
      <div class="plan-head">Broadcast <b>Package B</b></div>
      <div class="plan-price">$59.99</div>
      <ol><li>01. Awesome lorem ipsum dolor sit</li><li>02. Awesome lorem ipsum dolor sit</li><li>03. Awesome lorem ipsum dolor sit</li><li>04. Awesome lorem ipsum dolor sit</li><li>05. Awesome lorem ipsum dolor sit</li><li>06. Awesome lorem ipsum dolor sit</li></ol>
      <div class="plan-btn">SELECT PACKAGE</div>
    </div>
    <div class="plan" style="left:507px">
      <div class="plan-head">Broadcast <b>Package C</b></div>
      <div class="plan-price">$29.99</div>
      <ol><li>01. Awesome lorem ipsum dolor sit</li><li>02. Awesome lorem ipsum dolor sit</li><li>03. Awesome lorem ipsum dolor sit</li><li>04. Awesome lorem ipsum dolor sit</li><li>05. Awesome lorem ipsum dolor sit</li><li>06. Awesome lorem ipsum dolor sit</li></ol>
      <div class="plan-btn">SELECT PACKAGE</div>
    </div>
  </div>
</section>

<section class="design">
  <div class="sample-a" role="img" aria-label="Sample helicopter for sale broadcast ad"></div>
  <div class="sample-b" role="img" aria-label="Sample helicopter wanted broadcast ad"></div>
  <h2>Broadcast Design</h2>
  <p>Rotorbay Vista is one of most powerful marketing tools in the industry to utilize in reaching targeted buyers of pre-owned helicopters. Rotorbay Vista provides the rotor wing aircraft market with a fast, effective, and affordable email broadcast solution to utilize in the marketing of Helicopters for sale.</p>
  <div class="btn-proof">RECEIVE A DESIGN PROOF</div>
</section>

<footer class="site-footer">
  <div class="fcol" style="left:220px">
    <h4>CONTACT INFO</h4>
    228, lorem ipsum dolor,<br>dosis amet - 45895<br><br>T: 1800 555 0147<br>E: info@rotorbayvista.com
  </div>
  <div class="fcol" style="left:428px">
    <h4>QUICK LINKS</h4>
    Home<br>Services<br>Broadcast Design<br>Pricing<br>Contact
  </div>
  <div class="fcol" style="left:590px">
    <h4>HELPFUL LINKS</h4>
    Terms of Use<br>Privacy Policy<br>Sitemap<br>Contact Us
  </div>
  <div class="fcol" style="left:740px">
    <h4>SUBSCRIBE TO JOIN OUR MAILING LIST</h4>
  </div>
  <div class="signup"><span>Email Address</span><b>SUBSCRIBE</b></div>
  <div class="social"><span></span><span></span><span></span><span></span></div>
  <p class="copyright">Copyright © 2018 Rotorbay Vista. All Rights Reserved</p>
</footer>

</body>
</html>
```